Etikett für Rotweinflasche
Liebe farbkosmos Atelier, wir werden uns bei der endgültigen Etikettengestaltung (finale Größe + Rückseite) noch an Euch melden. Bitte sendet uns euren Kontakt an helga.brandt@morvelli.wine
Zielgruppe
Morvelli Italia ist ein exklusives Boutique-Weingut in Sizilien, das hochqualitative Spitzenweine in kleinen Mengen mit modernster Technologie und stets nachhaltig erzeugt. Wir hinterfragen sowohl in der Agronomie im Weingarten als auch in der Önologie im Weinkeller alle herrschenden Traditionen und trachten danach, stets das beste Endprodukt zu kreieren. Der vulkanische, kalkreiche Boden Siziliens sowie trockene, sonnenreiche und niederschlagsarme Vegetationsperioden sind unsere optimale Basis.
Zielgruppe: Internationale Genussmenschen jeglichen Alters, die sich bewusst auch höherpreisige Weine (um die €30+) gönnen , vor allem kunstaffine young professionals mit Qualitäts-& Nachhaltigkeitsanspruch
Aufgabenstellung
Das Etikett ist für Rotwein-Flaschen (Cabernet Sauvignon / Nero D'Avola / Frappato / Syrah / Cerasuolo / Petit Verdot / sowie einen Bourdeaux-Cuveè aus Cabernet Sauvignon und Petit Verdot) .
Die Flasche ist reinschwarz, sehr hochwertig und schwer.
Flaschenform: Bordeauxflasche siehe technisches Datenblatt
Sleeve über dem Korken: schwarz mit weißer Schrift wie bisher
Zu gestalten ist das Etikett der Vorderseite. Zumindest die jeweilige Rotwein-Sorte ist auch textlich darzustellen (zwecks Scannen mit Trubel-App)
Der Kreativität kann freien Lauf gelassen werden! Unterscheidbarkeit vom Markt ist explizit gewollt.
Unsere aktuellen Etiketten und Markenauftritt siehe: https://morvelli.wine/shop/

```html
<!DOCTYPE html>
<html lang="de">
<head>
<meta charset="utf-8">
<title>Etikett Cabernet Sauvignon</title>
<link rel="stylesheet" href="https://fonts.googleapis.com/css2?family=Cormorant+Garamond:wght@500&display=swap">
<style>
  :root {
    --canvas-bg: #ffffff;
    --mist-light: #f1e3f3;
    --mist-lilac: #d8b6df;
    --field-magenta: #b8326f;
    --field-violet: #7b4a93;
    --gown-red: #d81f2e;
    --label-text: #ffffff;
  }
  html, body {
    margin: 0;
    padding: 0;
    width: 849px;
    height: 1200px;
    overflow: hidden;
    background: var(--canvas-bg);
  }
  .canvas {
    position: relative;
    width: 849px;
    height: 1200px;
    display: flex;
    align-items: center;
    justify-content: center;
  }
  .front-label {
    position: relative;
    width: 760px;
    height: 451px;
    overflow: hidden;
  }
  .label-artwork {
    position: absolute;
    inset: 0;
    width: 100%;
    height: 100%;
    display: block;
  }
  .varietal-name {
    position: absolute;
    left: 0;
    right: 0;
    bottom: 38px;
    margin: 0;
    text-align: center;
    font-family: "Cormorant Garamond", "Times New Roman", serif;
    font-weight: 500;
    font-size: 26px;
    letter-spacing: 0.14em;
    color: var(--label-text);
  }
</style>
</head>
<body>
  <main class="canvas">
    <section class="front-label">
      <svg class="label-artwork" viewBox="0 0 760 451" preserveAspectRatio="none" role="img" aria-label="Fotografie: Frau in einem langen roten Kleid mit Schleppe in einem nebligen, rosa-violetten Wald">
        <defs>
          <linearGradient id="mist" x1="0" y1="0" x2="0" y2="1">
            <stop offset="0" stop-color="var(--mist-light)"/>
            <stop offset="0.45" stop-color="var(--mist-lilac)"/>
            <stop offset="0.72" stop-color="var(--field-magenta)"/>
            <stop offset="1" stop-color="var(--field-violet)"/>
          </linearGradient>
          <radialGradient id="gown" cx="0.5" cy="0.5" r="0.5">
            <stop offset="0" stop-color="var(--gown-red)" stop-opacity="0.9"/>
            <stop offset="1" stop-color="var(--gown-red)" stop-opacity="0"/>
          </radialGradient>
        </defs>
        <rect width="760" height="451" fill="url(#mist)"/>
        <ellipse cx="440" cy="280" rx="230" ry="90" fill="url(#gown)"/>
      </svg>
      <p class="varietal-name">CABERNET SAUVIGNON</p>
    </section>
  </main>
</body>
</html>
```